Oriel Photography Business Card

I need a business card designed for a photography business based in Perth, Western Australia called Oriel Photography.

We specialise in wedding, event photography and portrait photography.

The business card must borrow the style of the attached logo.

The hex codes for the colours in the logo are:
#ED1D85 - Pink
#89C23E - Green
#37282F - Black

The name on the card will be:
Name: Tobrian
Phone: 0417395268
Website: www.orielphotography.example.com.au
Facebook: orielphotography

I am open and happy to accept creative concepts.

I’d like some space at the back for writing notes and appointment details.

```html
<!DOCTYPE html>
<html lang="en">
<head>
<meta charset="utf-8">
<title>Oriel Photography – Business Card</title>
<link rel="stylesheet" href="https://fonts.googleapis.com/css2?family=Montserrat:wght@700&family=Questrial&display=swap">
<style>
  :root {
    --pink: #ED1D85;
    --green: #89C23E;
    --ink: #37282F;
    --white: #ffffff;
    --rule: #b9b4b6;
    --backdrop: #ebe8e4;
  }
  * { box-sizing: border-box; margin: 0; padding: 0; }
  html, body {
    width: 1200px;
    height: 720px;
    overflow: hidden;
    background: var(--backdrop);
  }
  .sheet {
    position: relative;
    width: 1200px;
    height: 720px;
    display: flex;
    align-items: center;
    justify-content: center;
    gap: 40px;
  }
  .card {
    position: relative;
    width: 540px;
    height: 330px;
    overflow: hidden;
    box-shadow: 0 6px 18px rgba(55, 40, 47, 0.18);
    font-family: "Questrial", sans-serif;
  }

  /* Front face */
  .card--front { background: var(--white); }
  .edge-accent {
    position: absolute;
    left: 0; top: 0;
    width: 22px; height: 330px;
  }
  .brand-mark {
    position: absolute;
    left: 142px; top: 34px;
    width: 56px; height: 56px;
    border-radius: 50%;
    background: var(--pink);
  }
  .brand-name {
    position: absolute;
    left: 58px; top: 112px;
    font-size: 17px;
    letter-spacing: 0.55em;
    color: var(--ink);
    text-transform: uppercase;
    white-space: nowrap;
  }
  .holder-name {
    position: absolute;
    right: 38px; top: 66px;
    font-family: "Montserrat", sans-serif;
    font-weight: 700;
    font-size: 21px;
    color: var(--pink);
    letter-spacing: 0.02em;
    text-transform: uppercase;
  }
  .contact-list {
    position: absolute;
    left: 46px; top: 224px;
    list-style: none;
  }
  .contact-item {
    display: flex;
    align-items: center;
    gap: 10px;
    height: 28px;
    font-size: 16px;
    color: var(--ink);
  }
  .contact-icon { width: 16px; height: 16px; flex: none; }

  /* Back face */
  .card--back { background: var(--pink); }
  .back-mark {
    position: absolute;
    left: 244px; top: 18px;
    width: 52px; height: 52px;
    border-radius: 50%;
    background: var(--white);
  }
  .back-brand {
    position: absolute;
    left: 0; right: 0; top: 84px;
    text-align: center;
    font-size: 15px;
    letter-spacing: 0.6em;
    color: var(--white);
    text-transform: uppercase;
  }
  .notes-box {
    position: absolute;
    left: 26px; top: 118px;
    width: 488px; height: 164px;
    background: var(--white);
    padding: 14px 22px 0;
  }
  .notes-line {
    height: 32px;
    border-bottom: 1px dotted var(--rule);
  }
  .notes-label {
    position: absolute;
    left: 22px; top: 98px;
    font-size: 19px;
    color: var(--ink);
    background: var(--white);
    padding-right: 6px;
  }
  .back-web {
    position: absolute;
    left: 0; right: 0; bottom: 16px;
    text-align: center;
    font-size: 15px;
    letter-spacing: 0.14em;
    color: var(--white);
  }
</style>
</head>
<body>
<main class="sheet">

  <section class="card card--front" aria-label="Business card front">
    <svg class="edge-accent" viewBox="0 0 22 330" aria-hidden="true">
      <polygon points="0,0 8,0 8,196 0,196" fill="var(--pink)"/>
      <polygon points="0,196 8,196 22,222 22,330 0,330" fill="var(--green)"/>
    </svg>

    <div class="brand-mark" aria-hidden="true"></div>
    <p class="brand-name">Oriel Photography</p>
    <p class="holder-name">Tobrian</p>

    <ul class="contact-list">
      <li class="contact-item">
        <svg class="contact-icon" viewBox="0 0 16 16" aria-hidden="true">
          <circle cx="8" cy="8" r="7" fill="none" stroke="var(--green)" stroke-width="1.5"/>
          <path d="M5.6 4.6c.4-.3.8-.2 1 .2l.6 1.1c.2.4.1.7-.2.9l-.4.3c.3.8.9 1.5 1.7 1.9l.3-.4c.2-.3.6-.4.9-.2l1.1.6c.4.2.5.6.2 1l-.5.6c-.4.4-1 .5-1.5.3C6.9 10.3 5.5 8.9 4.9 7c-.2-.5 0-1.1.3-1.5z" fill="var(--green)"/>
        </svg>
        <span>0417395268</span>
      </li>
      <li class="contact-item">
        <svg class="contact-icon" viewBox="0 0 16 16" aria-hidden="true">
          <rect x="1" y="1" width="14" height="14" rx="2" fill="var(--green)"/>
        </svg>
        <span>orielphotography</span>
      </li>
      <li class="contact-item">
        <svg class="contact-icon" viewBox="0 0 16 16" aria-hidden="true">
          <circle cx="8" cy="8" r="7" fill="var(--green)"/>
        </svg>
        <span>www.orielphotography.example.com.au</span>
      </li>
    </ul>
  </section>

  <section class="card card--back" aria-label="Business card back">
    <div class="back-mark" aria-hidden="true"></div>
    <p class="back-brand">Oriel Photography</p>

    <div class="notes-box">
      <div class="notes-line"></div>
      <div class="notes-line"></div>
      <div class="notes-line"></div>
      <div class="notes-line"></div>
      <span class="notes-label">notes:</span>
    </div>

    <p class="back-web">www.orielphotography.example.com.au</p>
  </section>

</main>
</body>
</html>
```